Infographic for a Christian church discipleship pathway

We need to take a fairly complex program that helps people in a Baptist church follow Jesus, and turn it into a simple graphic. This graphic does not have to explain the whole program, web pages and print materials will do that. But, it should be something that people see and understand what it is quickly. The attached graphic is only to give the key words and general direction of the program. It should not serve as a design guide. In other words, we want to see some other ideas how this information can be imparted graphically with concision and creativity. It's important to note, the categories at the top (pray daily, read daily, gather weekly) are first steps, starting points....one shouldn't move forward until they've incorporated these things into their life. However, the categories that follow (study, connect, serve, etc) are not necessarily steps to take in sequential order.

The diagrams we've provided are not what we expect. They are only to explain the program. Here is a verbal description: The motto of our church is "A Ready Church" (ready to serve, ready to love, ready for when Jesus returns). There are four words that describe a ready church member: FOCUSED on the return of Christ, FAITHFUL in a daily relationship with Jesus, PREPARED for any opportunity to be a supernatural vessel of God's worK, LOOKING to invite others into God's family. The first two are God's Work in Me (Focused and faithful); the second two are God's Work Through me (Prepared, looking). Please use those two things as you wish (Focused faithful prepared looking; and God's word in and through me). If they are clarifying, please use. If not, you don't have to use.

Additionally, the strategies we employ to be "a ready church" are 1. Prayer 2. God's Word, and 3. Biblical Community. (So, in other words, these three things help us be a people who is focused, faithful, prepared, and looking....which is a ready church.

To provide some information how we will build this out: this graphic will be used in print and digital content. The digital content will allow people to click on each category to access training and resources associated with that discipline. (Fasting, reflecting, etc).

www.kvt.church

Target Market(s)

35-50

Industry/Entity Type

Religious

Other font styles liked:
• Lato and/or Cambria

Requirements
Must have
• Fonts: lato, cambria. Colors#: 373E41, ebebe8, #a69677. Accent Colors: 80401D, #4e5730, #a5bac8
Nice to have
• A designer who has an understanding of what it means to incorporate the spiritual disciplines of the Christian faith into their life.

```html
<!DOCTYPE html>
<html lang="en">
<head>
<meta charset="utf-8">
<title>A Ready Church – Discipleship Pathway</title>
<link rel="stylesheet" href="https://fonts.googleapis.com/css2?family=Caladea:ital,wght@0,400;0,700;1,700&family=Lato:ital,wght@0,400;0,700;0,900;1,900&display=swap">
<style>
  :root{
    --ink:#373e41;
    --paper:#ffffff;
    --mist:#ebebe8;
    --mist-dark:#dcdbd6;
    --tan:#8a7c60;
    --tan-light:#a69677;
    --rust:#80401d;
    --rust-tab:#87522f;
    --olive:#4e5730;
    --olive-deep:#4a4b36;
    --slate-olive:#5a5b4e;
    --sky:#a5bac8;
    --steel:#3d5266;
    --cream:#efece2;
    --backdrop:#f3f3f1;
  }
  *{box-sizing:border-box;margin:0;padding:0}
  html,body{width:1200px;height:965px;overflow:hidden;background:var(--backdrop)}
  .poster{position:absolute;left:0;top:58px;width:1200px;height:848px;background:var(--paper);
    font-family:'Caladea',Cambria,Georgia,serif;color:var(--ink)}
  .abs{position:absolute}

  .church-name{left:44px;top:62px;font-weight:700;font-size:27px;line-height:27px;color:var(--ink);letter-spacing:.5px}
  .title{left:345px;top:42px;width:814px;text-align:center;font-weight:700;font-size:95px;line-height:95px;color:var(--olive);letter-spacing:1px;white-space:nowrap}
  .motto{left:341px;top:123px;width:818px;text-align:center;font-family:'Lato',sans-serif;font-size:20.5px;color:var(--rust);white-space:nowrap}

  .tab{top:184px;height:75px;width:216px;border-radius:9px 9px 0 0;display:flex;align-items:center;justify-content:center;
    text-align:center;font-weight:700;font-size:30px;line-height:30px;letter-spacing:.5px}
  .tab--prayer{left:283px;background:var(--sky);color:var(--olive)}
  .tab--word{left:579px;background:var(--tan);color:var(--cream)}
  .tab--community{left:880px;background:var(--rust-tab);color:var(--cream)}

  .column{top:320px;height:486px;background:var(--mist);border-radius:0 0 22px 22px;overflow:hidden}
  .column--prayer{left:248px;width:283px}
  .column--word{left:550px;width:283px}
  .column--community{left:854px;width:283px}
  .band{position:absolute;left:0;width:100%;background:var(--mist-dark)}
  .band--a{top:163px;height:79px}
  .band--b{top:323px;height:80px}

  .aims{left:229px;top:259px;width:931px;height:70px;background:var(--paper);box-shadow:0 4px 6px rgba(0,0,0,.22);display:flex}
  .aim{flex:1;display:flex;align-items:center;justify-content:center;text-align:center;font-weight:700;font-size:13px;line-height:17px;color:#1f2326;padding:0 20px}
  .aim + .aim{border-left:1px dashed #9aa0a3}
  .aim:first-child{flex:0 0 309px}
  .aim:nth-child(2){flex:0 0 305px}
  .pointer{position:absolute;top:328px;width:0;height:0;border-left:13px solid transparent;border-right:13px solid transparent;border-top:12px solid var(--paper)}

  .icon{top:361px;width:60px;height:60px;border-radius:50%;border:2px solid var(--paper);box-shadow:0 0 0 2px var(--ring)}
  .icon--prayer{left:360px;background:var(--tan);--ring:var(--rust)}
  .icon--word{left:667px;background:var(--rust);--ring:var(--tan)}
  .icon--community{left:966px;background:var(--steel);--ring:var(--tan)}

  .first-step{top:440px;font-weight:700;font-size:31px;line-height:31px;text-align:center;white-space:nowrap;letter-spacing:.3px}
  .first-step--prayer{left:248px;width:283px;color:var(--olive)}
  .first-step--word{left:550px;width:283px;color:var(--steel)}
  .first-step--community{left:854px;width:283px;color:var(--rust)}

  .step{font-weight:700;font-size:26px;line-height:26px;text-align:center;color:#1f2326;letter-spacing:.5px}

  .stage{left:44px;width:205px;display:flex;flex-direction:column;align-items:center;justify-content:center;text-align:center;color:var(--paper)}
  .stage--start{top:339px;height:144px;background:var(--tan);border-radius:18px 0 0 0}
  .stage--in{top:483px;height:160px;background:var(--slate-olive)}
  .stage--through{top:643px;height:159px;background:var(--olive-deep);border-radius:0 0 0 18px}
  .stage-words{font-weight:700;font-size:26px;line-height:25px;letter-spacing:.5px}
  .stage-note{font-weight:700;font-size:14.5px;margin-top:4px;letter-spacing:.3px}

  .divider{left:248px;top:643px;width:889px;border-top:1px dashed #5a5b4e}
  .arrows{left:0;top:0}
</style>
</head>
<body>
<main class="poster">
  <div class="abs church-name">KINGSVALE<br>TABERNACLE</div>
  <h1 class="abs title">A READY CHURCH</h1>
  <p class="abs motto">(READY TO SERVE, READY TO LOVE, READY FOR WHEN JESUS RETURNS)</p>

  <div class="abs tab tab--prayer">PRAYER</div>
  <div class="abs tab tab--word">GOD'S<br>WORD</div>
  <div class="abs tab tab--community">BIBLICAL<br>COMMUNITY</div>

  <div class="abs column column--prayer"><div class="band band--a"></div><div class="band band--b"></div></div>
  <div class="abs column column--word"><div class="band band--a"></div><div class="band band--b"></div></div>
  <div class="abs column column--community"><div class="band band--a"></div><div class="band band--b"></div></div>

  <div class="abs aims">
    <p class="aim">Become a person devoted to prayer<br>each day of your life.</p>
    <p class="aim">Build a daily habit of beholding God<br>in His Word.</p>
    <p class="aim">Engage deeply in Christian community.</p>
  </div>
  <span class="pointer" style="left:371px"></span>
  <span class="pointer" style="left:684px"></span>
  <span class="pointer" style="left:984px"></span>

  <div class="abs icon icon--prayer" role="img" aria-label="Praying hands with cross icon"></div>
  <div class="abs icon icon--word" role="img" aria-label="Open Bible icon"></div>
  <div class="abs icon icon--community" role="img" aria-label="Family gathering icon"></div>

  <div class="abs first-step first-step--prayer">PRAY DAILY</div>
  <div class="abs first-step first-step--word">READ DAILY</div>
  <div class="abs first-step first-step--community">GATHER WEEKLY</div>

  <div class="abs stage stage--start">
    <svg width="170" height="68" viewBox="0 0 170 68" aria-hidden="true">
      <polygon points="0,22 106,22 106,0 166,34 106,68 106,46 0,46" fill="var(--cream)"/>
    </svg>
    <span class="abs" style="left:21px;top:61px;font-family:'Lato',sans-serif;font-style:italic;font-weight:900;font-size:17px;color:#1f2326">START HERE</span>
  </div>
  <div class="abs stage stage--in">
    <div class="stage-words">FOCUSED<br>FAITHFUL</div>
    <div class="stage-note">God's Work In Me</div>
  </div>
  <div class="abs stage stage--through">
    <div class="stage-words">PREPARED<br>LOOKING</div>
    <div class="stage-note">God's Work Through Me</div>
  </div>

  <div class="abs divider"></div>

  <div class="abs step" style="left:248px;width:283px;top:506px">REST</div>
  <div class="abs step" style="left:248px;width:283px;top:587px">REFLECT</div>
  <div class="abs step" style="left:248px;width:283px;top:661px">FAST</div>
  <div class="abs step" style="left:248px;width:283px;top:744px">INTERCEDE</div>

  <div class="abs step" style="left:550px;width:283px;top:506px">STUDY</div>
  <div class="abs step" style="left:550px;width:283px;top:587px">MEMORIZE</div>
  <div class="abs step" style="left:550px;width:283px;top:661px">TEACH</div>
  <div class="abs step" style="left:550px;width:283px;top:744px">PROCLAIM</div>

  <div class="abs step" style="left:854px;width:283px;top:506px">CONNECT</div>
  <div class="abs step" style="left:854px;width:283px;top:587px">LEARN</div>
  <div class="abs step" style="left:854px;width:283px;top:661px">GIVE</div>
  <div class="abs step" style="left:854px;width:283px;top:744px">SERVE</div>

  <svg class="abs arrows" width="1200" height="848" viewBox="0 0 1200 848" aria-hidden="true">
    <defs>
      <g id="down">
        <line x1="0" y1="0" x2="0" y2="28" stroke-width="1.6"/>
        <polygon points="-4,22 4,22 0,34"/>
      </g>
    </defs>
    <g fill="var(--olive)" stroke="var(--olive)">
      <use href="#down" x="389" y="533"/><use href="#down" x="389" y="614"/><use href="#down" x="389" y="689"/>
    </g>
    <g fill="var(--rust)" stroke="var(--rust)">
      <use href="#down" x="691" y="533"/><use href="#down" x="691" y="614"/><use href="#down" x="691" y="689"/>
    </g>
    <g fill="var(--steel)" stroke="var(--steel)">
      <use href="#down" x="995" y="533"/><use href="#down" x="995" y="614"/><use href="#down" x="995" y="689"/>
    </g>
  </svg>
</main>
</body>
</html>
```